Kelvaro.ch is looking for business card letterhead and envelope C5 with WOW effect

We need a strong business card for our company Kelvaro.ch, logo is available. You want a black or dark background on which the logo Stark r% 26 # 252; appears. Letterhead and envelope in C5 format should be in a similar design, but does not have to be We need a strong business card for our company Kelvaro.ch, logo is available. A black or dark background is desired, on which the logo Stark comes across. The letterhead and the envelope in C5 format should have a similar design.

Target Market(s)

Private customers as well as entrepreneurs

Contact Information for Business Card

E-mail: info@kelvaro-example.ch
Web.www.Kelvaro-example.ch
Tel: +41 ( 0 ) 79 482 6037
Adresse:
Lindenweg 14
9406 Tarnbach

Hier kann man Icons verwenden für Email,Tel und Adressse

Font styles to use
Other font styles liked:
• Dubai,bold

Colors

Designer to choose colors to be used in the design.

Requirements
Must have
• WOW effect
Nice to have
• R% 26 # 252; back business card with our service listings. - VEHICLE LABELING - SHOP WINDOW LABELING - STICKERS AND MUCH MORE ... in red color

```html
<!DOCTYPE html>
<html lang="de">
<head>
<meta charset="utf-8">
<title>Kelvaro.ch – Visitenkarte</title>
<link rel="stylesheet" href="https://fonts.googleapis.com/css2?family=Exo+2:wght@600&family=Montserrat:wght@400;500;700&display=swap">
<style>
  :root{
    --stage:#e7e4df;
    --card:#1b1c1e;
    --card-edge:#232427;
    --accent:#f7c51e;
    --text:#ffffff;
    --muted:#d9d9d9;
    --divider:#8a8a8a;
  }
  *{box-sizing:border-box;margin:0;padding:0}
  html,body{width:1200px;height:700px;overflow:hidden;background:var(--stage)}
  body{position:relative;font-family:"Montserrat",Arial,sans-serif}

  .card{
    position:absolute;top:195px;width:540px;height:310px;
    background:var(--card);
    box-shadow:0 6px 18px rgba(0,0,0,.25);
    overflow:hidden;
  }
  .card--front{left:40px}
  .card--back{left:620px}

  /* front */
  .brand{
    position:absolute;left:0;right:0;top:108px;
    display:flex;align-items:center;justify-content:center;gap:14px;
  }
  .brand__mark{width:34px;height:34px;background:var(--accent)}
  .brand__name{
    color:var(--text);font-weight:700;font-size:40px;letter-spacing:1px;
  }
  .services{
    position:absolute;left:0;right:0;bottom:56px;
    display:flex;justify-content:center;align-items:center;gap:8px;
    color:var(--text);font-size:14px;font-weight:500;letter-spacing:.3px;
  }
  .services__dot{width:7px;height:7px;border-radius:50%;background:var(--accent)}

  /* back */
  .network{
    position:absolute;inset:0;
    background:radial-gradient(ellipse at 30% 40%,#26251f 0%,var(--card-edge) 45%,var(--card) 100%);
  }
  .person{
    position:absolute;top:138px;right:277px;text-align:right;
  }
  .person__name{
    font-family:"Exo 2",Arial,sans-serif;font-weight:600;
    color:var(--accent);font-size:23px;line-height:1.1;
  }
  .person__role{color:var(--text);font-size:15px;font-weight:500;margin-top:4px}
  .divider{
    position:absolute;left:282px;top:134px;width:1px;height:56px;background:var(--divider);
  }
  .contacts{
    position:absolute;left:300px;top:135px;list-style:none;
    color:var(--text);font-size:12.5px;font-weight:500;
  }
  .contacts li{display:flex;align-items:center;gap:8px;height:17px}
  .icon{width:10px;height:10px;flex:none;fill:var(--accent)}
  .address{
    position:absolute;left:0;right:0;top:262px;
    display:flex;justify-content:center;align-items:center;gap:8px;
    color:var(--text);font-size:12.5px;font-weight:500;
  }
</style>
</head>
<body>

<section class="card card--front">
  <div class="brand">
    <span class="brand__mark"></span>
    <span class="brand__name">KELVARO.CH</span>
  </div>
  <div class="services">
    <span>Vehicle Labeling</span><span class="services__dot"></span>
    <span>Shop Window Labeling</span><span class="services__dot"></span>
    <span>Stickers</span>
  </div>
</section>

<section class="card card--back">
  <div class="network" role="img" aria-label="Feines Netz aus dünnen goldenen Verbindungslinien als Hintergrundmuster"></div>

  <div class="person">
    <p class="person__name">Jonas Berger</p>
    <p class="person__role">President</p>
  </div>
  <div class="divider"></div>

  <ul class="contacts">
    <li>
      <svg class="icon" viewBox="0 0 24 24"><path d="M6.6 10.8a15 15 0 0 0 6.6 6.6l2.2-2.2a1 1 0 0 1 1-.25 11.4 11.4 0 0 0 3.6.57 1 1 0 0 1 1 1V20a1 1 0 0 1-1 1A17 17 0 0 1 3 4a1 1 0 0 1 1-1h3.5a1 1 0 0 1 1 1c0 1.25.2 2.45.57 3.57a1 1 0 0 1-.25 1z"/></svg>
      <span>+41 ( 0 ) 79 482 6037</span>
    </li>
    <li>
      <svg class="icon" viewBox="0 0 24 24"><path d="M2 5h20v14H2z M3 6l9 7 9-7" /><path d="M2 5l10 8 10-8v1l-10 8L2 6z" fill="#1b1c1e"/></svg>
      <span>info@kelvaro-example.ch</span>
    </li>
    <li>
      <svg class="icon" viewBox="0 0 24 24"><circle cx="12" cy="12" r="10"/><path d="M2 12h20M12 2c3 3 3 17 0 20M12 2c-3 3-3 17 0 20" stroke="#1b1c1e" stroke-width="1.6" fill="none"/></svg>
      <span>www.Kelvaro-example.ch</span>
    </li>
  </ul>

  <div class="address">
    <svg class="icon" viewBox="0 0 24 24" style="width:11px;height:13px"><path d="M12 1a8 8 0 0 0-8 8c0 6 8 14 8 14s8-8 8-14a8 8 0 0 0-8-8zm0 11a3 3 0 1 1 0-6 3 3 0 0 1 0 6z"/></svg>
    <span>Lindenweg 14 9406 Tarnbach</span>
  </div>
</section>

</body>
</html>
```